Redesign a Start-Up Dating Website

Website: https://morvelique.com.
Make sure the design has an island style theme.
I would like the 7 pages of my website to have a new and professional look. I want the same colors to remain, but I want a creative look for all the pages. This is a dating website that is in the startup stage. So, I want to give my entire website a custom makeover. I want something that will stand out from the other dating sites. Something that will attract more people to want to use my services, and hopefully get new members.
Target Market(s)
Dating
Industry/Entity Type
Dating
Coding
Coded - Design and coding required
Number of Pages Required
5+ page
Font styles to use
Other font styles liked:
- Decorative, San Serif
Requirements
Must have
- The design must have the original colors and a stylish font to go along. The design must be creative, welcoming, and professional. I would like an island style theme for the website. This is a dating website so make sure that the design is tailored to that aspect.
Nice to have
- It would be nice to have a decorative font and a professional style on all the pages. Make sure the design will be mobile responsive and friendly for all the pages on the website.
Should not have
- The design should not be bland and uncreative.

```html
<!DOCTYPE html>
<html lang="en">
<head>
<meta charset="utf-8">
<title>Morvelique — Dating</title>
<link href="https://fonts.googleapis.com/css2?family=Courgette&family=Open+Sans:wght@400;600;700&display=swap" rel="stylesheet">
<style>
:root{
  --teal:#2bb3a3;
  --teal-dark:#1f9c8e;
  --orange:#f7941d;
  --purple:#6a4c9c;
  --ink:#333333;
  --muted:#777777;
  --dark:#2b2b2b;
  --white:#ffffff;
}
*{margin:0;padding:0;box-sizing:border-box}
html,body{width:1200px;height:2872px;overflow:hidden}
body{font-family:"Open Sans",Arial,sans-serif;color:var(--ink);background:var(--white);position:relative}
.script{font-family:"Courgette",cursive}

/* header */
.site-header{height:88px;background:var(--teal);display:flex;align-items:center;justify-content:space-between;padding:0 70px}
.brand{display:flex;align-items:center;gap:12px;color:var(--white);font-weight:700;font-size:28px}
.brand-dot{width:36px;height:36px;border-radius:50%;background:var(--orange)}
.main-nav{display:flex;gap:34px;font-size:13px;font-weight:600;color:var(--white);letter-spacing:.5px}
.main-nav .active{color:var(--orange)}
.main-nav .account{color:var(--orange)}

/* hero */
.hero{height:372px;position:relative;background:linear-gradient(100deg,#7a6a58 0%,#b59a78 35%,#d9b98f 60%,#8a6b4e 100%)}
.hero-copy{position:absolute;left:70px;top:80px}
.hero-title{font-size:46px;line-height:1.25;color:var(--white)}
.hero-title span{color:var(--orange)}
.btn{display:inline-block;border-radius:4px;color:var(--white);font-weight:600;font-size:14px;text-align:center}
.btn-orange{background:var(--orange)}
.btn-purple{background:var(--purple)}
.hero .btn{margin-top:28px;padding:12px 34px}

/* search */
.search-bar{height:80px;background:var(--teal);display:flex;align-items:center;justify-content:center;gap:14px;color:var(--white);font-size:13px}
.select{background:var(--white);color:var(--ink);border-radius:3px;height:30px;padding:0 10px;display:flex;align-items:center;justify-content:space-between;gap:10px;font-size:12px}
.select::after{content:"";border:4px solid transparent;border-top-color:var(--ink);margin-top:4px}
.search-bar .btn{padding:8px 26px;margin-left:10px}

/* section titles */
.section-title{text-align:center;font-size:34px;color:var(--ink)}
.divider{display:block;margin:10px auto 0}

/* how it works */
.how{height:820px;position:relative;padding-top:120px}
.how .lead{text-align:center;color:var(--muted);font-size:14px;font-style:italic;margin-top:20px}
.timeline{position:absolute;left:599px;top:300px;width:2px;height:390px;background:#cfcfcf}
.step-icon{position:absolute;left:555px;width:90px;height:90px;border-radius:50%;border:4px solid var(--white);box-shadow:0 0 0 2px #dedede}
.icon-a{top:296px;background:var(--orange)}
.icon-b{top:466px;background:var(--purple)}
.icon-c{top:616px;background:#f6c9a3}
.step{position:absolute;width:260px}
.step h3{font-size:16px;font-weight:700;margin-bottom:8px}
.step p{font-size:12px;line-height:1.6;color:var(--muted)}
.step-a{left:170px;top:300px}
.step-b{left:680px;top:470px}
.step-c{left:170px;top:640px}

/* promo band */
.promo{height:440px;background:var(--orange);text-align:center;color:var(--white);padding-top:100px}
.promo h2{font-size:34px;font-weight:400}
.promo p{font-size:14px;font-weight:600;line-height:1.8;margin:40px auto 0;width:560px}
.promo .btn{margin-top:26px;padding:14px 34px}

/* users */
.users{height:620px;padding-top:60px;text-align:center}
.user-list{display:flex;justify-content:center;gap:32px;margin-top:56px}
.user{width:180px}
.user-photo{height:180px}
.user-name{font-size:15px;font-weight:600;margin-top:16px}
.user-place{font-size:12px;color:var(--muted);margin-top:4px}
.users .btn{margin-top:56px;padding:14px 30px}

/* signup */
.signup{height:340px;background:var(--dark);display:flex}
.signup-photo{width:560px;height:100%;background:linear-gradient(90deg,#3a2c24,#8a5e44 55%,#3a2c24)}
.signup-form{padding:90px 0 0 60px}
.signup-form h2{color:var(--orange);font-size:26px;font-weight:600;letter-spacing:1px}
.form-row{display:flex;gap:18px;margin-top:22px}
.email-field{width:300px;height:50px;border:2px solid var(--white);color:#bbbbbb;font-size:14px;display:flex;align-items:center;padding:0 16px}
.signup .btn{width:170px;height:50px;line-height:50px;font-size:18px}

/* footer */
.site-footer{height:112px;background:var(--teal);color:var(--white);position:relative}
.footer-nav{display:flex;justify-content:center;gap:70px;font-size:12px;font-weight:600;padding-top:34px}
.footer-bottom{position:absolute;left:70px;right:70px;bottom:18px;display:flex;justify-content:space-between;align-items:center;font-size:11px}
.social{display:flex;gap:12px}
.social span{width:14px;height:14px;border-radius:50%;background:var(--white)}
</style>
</head>
<body>

<header class="site-header">
  <div class="brand"><span class="brand-dot"></span>Morvelique</div>
  <nav class="main-nav">
    <span class="active">HOME</span><span>MEMBERS</span><span>EXTRAS</span><span>ABOUT</span><span>PREMIUM</span><span>CONTACT</span><span class="account">LOGIN &nbsp;|&nbsp; REGISTER</span>
  </nav>
</header>

<section class="hero" role="img" aria-label="Photo of a young couple outdoors, a man playing guitar for a smiling woman holding flowers">
  <div class="hero-copy">
    <h1 class="hero-title script">Let's Find Your<br><span>Perfect Match Now</span></h1>
    <span class="btn btn-orange">Join us!</span>
  </div>
</section>

<section class="search-bar">
  <span>I am a</span><span class="select" style="width:80px">Man</span>
  <span>Seeking a</span><span class="select" style="width:90px">Woman</span>
  <span>From</span><span class="select" style="width:56px">18</span>
  <span>to</span><span class="select" style="width:56px">30</span>
  <span>Country</span><span class="select" style="width:130px">Afghanistan</span>
  <span class="btn btn-orange">Search</span>
</section>

<section class="how">
  <h2 class="section-title script">Dating is Easy with Morvelique</h2>
  <svg class="divider" width="200" height="16" viewBox="0 0 200 16"><line x1="0" y1="8" x2="88" y2="8" stroke="#f7941d" stroke-width="2"/><line x1="112" y1="8" x2="200" y2="8" stroke="#f7941d" stroke-width="2"/><path d="M100 15 L92 7 A4 4 0 0 1 100 3 A4 4 0 0 1 108 7 Z" fill="#f7941d"/></svg>
  <p class="lead">Neque porro quisquam est qui dolorem ipsum quia dolor sit amet, consectetur, adipisci velit...</p>

  <div class="timeline"></div>
  <div class="step-icon icon-a" role="img" aria-label="Illustration of a man creating a profile"></div>
  <div class="step-icon icon-b" role="img" aria-label="Illustration of a woman finding matches"></div>
  <div class="step-icon icon-c" role="img" aria-label="Illustration of a couple starting to date"></div>

  <div class="step step-a"><h3>Create a Profile</h3><p>Let people know all about you, the good and the quirky. Share the world your true colors and find someone with the same unique qualities as you.</p></div>
  <div class="step step-b"><h3>Find Matches</h3><p>Browse other users and feel the excitement of getting your first message and getting to know potential dates in a calm and fun environment.</p></div>
  <div class="step step-c"><h3>Start Dating</h3><p>Once you've found your potential soulmate, it's time to meet up and say hello to the start of your journey together.</p></div>
</section>

<section class="promo">
  <h2 class="script">Start Dating Singles Today!</h2>
  <svg class="divider" width="200" height="16" viewBox="0 0 200 16"><line x1="0" y1="8" x2="88" y2="8" stroke="#fff" stroke-width="2"/><line x1="112" y1="8" x2="200" y2="8" stroke="#fff" stroke-width="2"/><path d="M100 15 L92 7 A4 4 0 0 1 100 3 A4 4 0 0 1 108 7 Z" fill="#fff"/></svg>
  <p>SIGN UP FOR A 30 DAYS FREE TRIAL<br>ENJOY ALL THE BENEFITS MORVELIQUE HAS TO OFFER WITH A FULL MEMBERSHIP</p>
  <span class="btn btn-purple">Start Morveliquing with Free Sign Up</span>
</section>

<section class="users">
  <h2 class="section-title script">Last 5 Registered Users</h2>
  <svg class="divider" width="200" height="16" viewBox="0 0 200 16"><line x1="0" y1="8" x2="88" y2="8" stroke="#f7941d" stroke-width="2"/><line x1="112" y1="8" x2="200" y2="8" stroke="#f7941d" stroke-width="2"/><path d="M100 15 L92 7 A4 4 0 0 1 100 3 A4 4 0 0 1 108 7 Z" fill="#f7941d"/></svg>
  <div class="user-list">
    <div class="user"><div class="user-photo" role="img" aria-label="Portrait photo of a bearded man" style="background:linear-gradient(160deg,#8d7d70,#4a3f38)"></div><p class="user-name">Darren K Wexley</p><p class="user-place">Michigan</p></div>
    <div class="user"><div class="user-photo" role="img" aria-label="Portrait photo of a blonde woman" style="background:linear-gradient(160deg,#d8c3a0,#9b8366)"></div><p class="user-name">Callie R Fenmore</p><p class="user-place">Florida</p></div>
    <div class="user"><div class="user-photo" role="img" aria-label="Portrait photo of a young man in a white shirt" style="background:linear-gradient(160deg,#c9c9c4,#7f7a74)"></div><p class="user-name">Victor P Almoran</p><p class="user-place">Kentucky</p></div>
    <div class="user"><div class="user-photo" role="img" aria-label="Portrait photo of a woman covering her eyes" style="background:linear-gradient(160deg,#e9e4dc,#b7a99a)"></div><p class="user-name">Nadia E Quill</p><p class="user-place">Michigan</p></div>
    <div class="user"><div class="user-photo" role="img" aria-label="Portrait photo of a man with a beard" style="background:linear-gradient(160deg,#a59a90,#5c524b)"></div><p class="user-name">Tobias H Carrow</p><p class="user-place">Michigan</p></div>
  </div>
  <span class="btn btn-purple">Join Now</span>
</section>

<section class="signup">
  <div class="signup-photo" role="img" aria-label="Photo of a smiling couple embracing in warm evening light"></div>
  <div class="signup-form">
    <h2>SIGNUP NOW</h2>
    <div class="form-row">
      <div class="email-field">Email Address</div>
      <span class="btn btn-purple">SUBMIT</span>
    </div>
  </div>
</section>

<footer class="site-footer">
  <nav class="footer-nav"><span>HOME</span><span>MEMBERS</span><span>EXTRAS</span><span>ABOUT</span><span>PREMIUM</span><span>CONTACT</span></nav>
  <div class="footer-bottom">
    <span>Copyright © 2017 Morvelique All Rights Reserved</span>
    <div class="social"><span></span><span></span><span></span><span></span></div>
  </div>
</footer>

</body>
</html>
```